House Cleaning Platform for Consumers and Cleaners

UPDATE: I've attached screenshots showing a purchase flow example, something all designers have missed in their designs. PLEASE check the URLs I've included in the brief for examples of a cleaning website. I've seen mostly landing pages and nothing else.

WHAT I'M LOOKING FOR:
I need the UI designed for a house cleaning web platform from 2 separate experiences: one from the consumer end to order a cleaner to come clean their house and one from a cleaner’s end that manages their orders and manages their schedule.

The UI will need to include photo uploading for before and after photos, a checkout/cart experience w/ tips, toggle options for adding and removing rooms/extras cleaning add-ons, customer+cleaner reviews (meaning the cleaner finished the job and they can rate and review the customer as well as the customer can rate and review the cleaner), order history for consumers, job history for cleaners, profile, settings, and landing pages for both.

PLEASE DO NOT USE THE COLOR BLUE AS THE PRIMARY COLOR. Use a light green (HEX #2fdf86) instead for primary theming color.

REFERENCES:
If you'd like a few websites I've enjoyed for references, checkout:
larkpolish.example, vomby.example, and brightfernhome.example.

For sake of branding, the company name is PlumNest. Currently do not have a logo as we have not decided on the name. Logo will come later.

Feel free to reach out to me if you have any questions!
Updates

Most designer submissions were a landing page and only a landing page. Very few designed the flows I requested and none designed a schedule management page. I even updated the Brief to more clearly outline the needs and references. Only about 2-3 of the designers actually did more than a landing page. Still don't believe I received 6 designers input that I had paid for.

Target Market(s)

FULL-TIME WORKING HOUSEHOLDS, SINGLE PROFESSIONALS, SINGLE PARENTS, ELDERLY & MOBILITY CHALLENGED, BUSY BODIES.

Industry/Entity Type

Cleaning, gig work.

Number of Pages Required

5+ page

Font styles to use
Other font styles liked:
• Jost or Lexend are great Google Font options I've used in the pitch deck and horribly done app mockups.

Colors
00AB8E
00BBA5
67D7C9
C6EFE9
E9F9F6
59FF00
82FF00
B8FF75
E3FFCB
F4FFEA
FFF300
FFF600
FEFA6F
FFFEC7
FFFEE8
FFC000
F8CF3A
FAE287
FDF2CF
FEFAEE

Requirements
Must have
• Landing page, consumer flow, cleaner schedule management, checkout flow, Rate & Review for consumer and/or cleaner, order history, profile.
Nice to have
• I'd like it to be simple in design and modern, but not so simple it's boring. Iconography can sometimes break that up, but I don't want it looking busy. It's a cleaning platform so the UI should look clean.

```html
<!DOCTYPE html>
<html lang="en">
<head>
<meta charset="UTF-8">
<title>PlumNest – Book Your Services</title>
<link href="https://fonts.googleapis.com/css2?family=Nunito:wght@400;600;700;800&family=Open+Sans:wght@700&display=swap" rel="stylesheet">
<style>
  :root {
    --green: #27d383;
    --dark: #3a3a3a;
    --ink: #111111;
    --muted: #444444;
    --card-bg: #f6f6f6;
    --orange: #f7941d;
    --white: #ffffff;
    --border: #dddddd;
  }
  * { box-sizing: border-box; margin: 0; padding: 0; }
  html, body { width: 1200px; height: 858px; overflow: hidden; background: var(--white); }
  body { position: relative; font-family: 'Nunito', sans-serif; color: var(--ink); }

  .site-header { position: absolute; top: 0; left: 0; width: 1200px; height: 70px; }
  .brand { position: absolute; left: 101px; top: 17px; font-family: 'Nunito', sans-serif; font-weight: 800; font-size: 29px; color: var(--green); }
  .main-nav { position: absolute; left: 438px; top: 26px; display: flex; gap: 19px; font-size: 12px; font-weight: 600; }
  .search { position: absolute; left: 731px; top: 22px; width: 218px; height: 25px; border: 1px solid var(--border); border-radius: 13px; display: flex; align-items: center; padding-left: 8px; gap: 14px; font-size: 12px; font-weight: 600; }
  .login { position: absolute; left: 981px; top: 26px; font-size: 12px; font-weight: 600; }
  .signup { position: absolute; left: 1024px; top: 22px; width: 75px; height: 25px; border-radius: 13px; background: var(--green); font-size: 11px; font-weight: 600; display: flex; align-items: center; justify-content: center; }

  .page-title { position: absolute; top: 127px; width: 1200px; text-align: center; font-family: 'Open Sans', sans-serif; font-weight: 700; font-size: 37px; letter-spacing: -0.2px; }
  .divider { position: absolute; top: 215px; left: 0; width: 1200px; height: 1px; background: var(--green); }

  .section-head { position: absolute; left: 101px; top: 282px; display: flex; align-items: center; gap: 14px; font-size: 20px; font-weight: 600; }
  .section-sub { position: absolute; left: 101px; top: 321px; font-size: 11.5px; color: var(--muted); }

  .plan { position: absolute; top: 370px; width: 234px; height: 281px; border-radius: 5px; background: var(--card-bg); overflow: hidden; }
  .plan-head { height: 74px; background: var(--dark); color: var(--white); display: flex; align-items: center; justify-content: center; font-weight: 800; font-size: 23px; letter-spacing: 0.3px; }
  .plan-name { margin-top: 33px; text-align: center; font-size: 16px; font-weight: 600; }
  .plan-text { margin: 16px auto 0; width: 190px; text-align: center; font-size: 11.5px; line-height: 18.2px; color: var(--muted); }
  .plan.is-selected { background: var(--white); border: 1px solid var(--green); }
  .plan.is-selected .plan-head { background: var(--green); margin: -1px -1px 0; }
  .ribbon { position: absolute; left: 310px; top: 364px; width: 16px; height: 62px; }

  .btn { position: absolute; top: 714px; width: 175px; height: 50px; border-radius: 25px; display: flex; align-items: center; justify-content: center; font-size: 16px; font-weight: 600; }
  .btn-back { left: 101px; border: 1px solid var(--border); }
  .btn-next { left: 307px; background: var(--green); }
</style>
</head>
<body>
  <header class="site-header">
    <div class="brand">PlumNest</div>
    <nav class="main-nav"><span>Home</span><span>Pricing</span><span>Services</span><span>Contact</span><span>Help</span></nav>
    <div class="search">
      <svg width="14" height="14" viewBox="0 0 14 14" fill="none" stroke="#222" stroke-width="1.2"><circle cx="6" cy="6" r="5"/><path d="M9.7 9.7 13 13"/></svg>
      <span>Search</span>
    </div>
    <span class="login">Login</span>
    <span class="signup">Sign Up</span>
  </header>

  <h1 class="page-title">Book Your Services Now</h1>
  <div class="divider"></div>

  <div class="section-head">
    <svg width="14" height="12" viewBox="0 0 14 12" fill="none" stroke="#27d383" stroke-width="1.2" stroke-linecap="round"><path d="M1 5V4a2 2 0 0 1 2-2h9M10 0l2 2-2 2M13 7v1a2 2 0 0 1-2 2H2M4 12l-2-2 2-2"/></svg>
    <span>Frequency</span>
  </div>
  <p class="section-sub">How often do you want services?</p>

  <article class="plan" style="left:101px">
    <div class="plan-head">10% Discount</div>
    <h3 class="plan-name">Every Two Weeks</h3>
    <p class="plan-text">Lorem Ipsum Dolor Sit Amet Consectetur. Facilisis Ut Faucibus Ipsum Non. Elementum Felis Quam Sed Leo Malesuada Molestie Adipiscing Erat Lorem. Non Neque.</p>
  </article>
  <svg class="ribbon" viewBox="0 0 16 62"><path d="M0 0h16v62l-8-9-8 9z" fill="#f7941d"/><text x="11" y="41" transform="rotate(-90 11 41)" font-family="Nunito, sans-serif" font-size="5.5" font-weight="800" fill="#fff" letter-spacing="0.4">POPULAR</text></svg>

  <article class="plan" style="left:357px">
    <div class="plan-head">5% Discount</div>
    <h3 class="plan-name">Every Four Weeks</h3>
    <p class="plan-text">Lorem Ipsum Dolor Sit Amet Consectetur. Facilisis Ut Faucibus Ipsum Non. Elementum Felis Quam Sed Leo Malesuada Molestie Adipiscing Erat Lorem. Non Neque.</p>
  </article>

  <article class="plan is-selected" style="left:614px">
    <div class="plan-head">15% Discount</div>
    <h3 class="plan-name">Weekly</h3>
    <p class="plan-text">Lorem Ipsum Dolor Sit Amet Consectetur. Facilisis Ut Faucibus Ipsum Non. Elementum Felis Quam Sed Leo Malesuada Molestie Adipiscing Erat Lorem. Non Neque.</p>
  </article>

  <article class="plan" style="left:870px">
    <div class="plan-head">No Discount</div>
    <h3 class="plan-name">One Time</h3>
    <p class="plan-text">Lorem Ipsum Dolor Sit Amet Consectetur. Facilisis Ut Faucibus Ipsum Non. Elementum Felis Quam Sed Leo Malesuada Molestie Adipiscing Erat Lorem. Non Neque.</p>
  </article>

  <a class="btn btn-back">Back</a>
  <a class="btn btn-next">Save &amp; Next</a>
</body>
</html>
```